Doctor Formulated Medical Cosmetics

Velour Skinhaus is an E-commerce site for high end Medical Cosmetics designed to treat specific skin problems. The Velour Skinhaus difference/advantage is that all creams and serums are:
Doctor Formulated, Freshly Handmade, Registered Pharmacy.
The Site also provides real doctor Dermatology Consultations, Library (with a list of - 1. Active Ingredients in the creams with description of their effects, 2. Skin Conditions with information on what causes the condition and typical treatment approaches and outcomes. 3. Resources from Dermatology Journals and literature on the conditions.)
Header Information: Velour Skinhaus, languages EN, BG, Register / log in, Shopping Bag. This field should be narrow.
Categories (horizontal): Home, Face, Body, Hair Care, Skin Conditions, Doctor Consultation, Library
The Landing Page should have only one well organized picture, which is intended to create the feeling of luxury, freedom and relaxation. It will be large and will fill the whole screen. All text should be on transparent or similar color fields. Please use the color of the text to create also the feeling of conservative luxury.
Written message / image overlay Velour Skinhaus(logo), Skin Care, Doctor Formulated, Freshly Handmade, Registered Pharmacy.
Please study the Landing Page of this site as an example: www.marivane.com
Under the Landing Page, there should be a slider with 4 of our products.
Underneath: Four Blog Articles (large pictures for maximum impact and luxury text underneath).
Underneath: Banner for Dermatologist Consultation, (button for Start Your Case Now).
Underneath: Two pictures in a line - Library (with books), and Active Ingredients.
Footer: Philosophy, Categories, Customer Care
Please adhere to the color palate provided in the pictures (as attachments). Provided are some examples of Web Sites with the desired look and feel. www.quillora.com , www.tavenholtmd.com .
Please use different shades of gray, white, beige and gold colors, and black. Our products will be in brown glass jars and bottles to convey the professional, pharmacy made nature of the creams and lotions.
We find the following Front Page very attractive and effective - www.marivane.com , with its full page image and overlaying text.
Please have a look at this link for the Landing page.
http://www.brimlensphoto.com/detail/video/woman-lying-on-a-black-sand-beach-in-a-bikini-stock-footage/58213067
I would like to use it in the animated version to achieve the WOW effect. I have uploaded the jpeg version for it, so you will be able create your design.
For the Landing page design, please use only the two uploaded pictures of a woman laying at the beach. Let's see how each of them will look like.
Thank you for your help.

```html
<!DOCTYPE html>
<html lang="en">
<head>
<meta charset="utf-8">
<title>Velour Skinhaus — Doctor Formulated Medical Cosmetics</title>
<link href="https://fonts.googleapis.com/css2?family=Questrial&family=Didact+Gothic&family=Lato:wght@400;700&display=swap" rel="stylesheet">
<style>
:root{
  --gold:#c9a35b;
  --gold-soft:#dcc28f;
  --brown:#5a4e45;
  --brown-dark:#4a3f37;
  --ink:#2f2f2f;
  --muted:#6f6f6f;
  --line:#d6d6d6;
  --panel:#f1f1f1;
  --white:#ffffff;
  --footer:#232323;
  --footer-bar:#151515;
  --footer-text:#cfcfcf;
}
*{box-sizing:border-box;margin:0;padding:0}
html,body{width:1200px;height:2338px;overflow:hidden;background:var(--white)}
body{font-family:"Lato",sans-serif;color:var(--ink);position:relative}
.abs{position:absolute}
a{color:inherit;text-decoration:none}

/* top bar */
.topbar{top:0;left:0;width:1200px;height:47px;background:var(--white);font-size:12px;color:#444}
.topbar .item{top:15px;display:flex;align-items:center;gap:7px}
.topbar svg{width:16px;height:16px;fill:#555}
.lang{top:10px;left:1028px;width:92px;height:26px;border:1px solid #999;display:flex;align-items:center;gap:6px;padding:0 6px;font-size:12px}
.lang .flag{width:16px;height:11px;background:#8a8fa8}

/* header */
.header{top:47px;left:0;width:1200px;height:112px;background:var(--white)}
.logo{left:80px;top:22px;display:flex;align-items:center;gap:12px;font-family:"Questrial",sans-serif;font-size:42px;color:var(--gold)}
.logo .mark{width:64px;height:64px;border-radius:50%;border:2px solid var(--gold)}
.contact{display:flex;align-items:center;gap:14px;top:32px}
.contact .disc{width:38px;height:38px;border-radius:50%;background:var(--brown-dark);display:flex;align-items:center;justify-content:center}
.contact .disc svg{width:20px;height:20px;fill:#fff}
.contact small{display:block;font-size:12px;color:var(--gold)}
.contact strong{font-weight:400;font-size:18px;color:#222}

/* nav */
.nav{top:159px;left:0;width:1200px;height:48px;background:var(--brown);display:flex;align-items:center;padding-left:85px;gap:0;font-size:15px;color:#f3ede6}
.nav a{margin-right:0}
.nav a.current{border-bottom:1px solid #fff;padding-bottom:3px}

/* hero */
.hero{top:207px;left:0;width:1200px;height:527px;background:linear-gradient(90deg,#f3d5d8 0%,#f4c4c8 45%,#f2b4b9 100%)}
.hero-photo{left:30px;top:0;width:510px;height:527px;background:radial-gradient(ellipse at 45% 40%,#f2d8cc 0%,#e7bfb4 50%,#f3d0d2 100%)}
.hero-products{left:740px;top:45px;width:440px;height:300px;background:radial-gradient(ellipse at 50% 55%,#f4f1f5 0%,#e3dff0 45%,rgba(242,180,185,0) 75%)}
.hero-title{right:83px;top:405px;text-align:right;font-family:"Didact Gothic",sans-serif;font-size:35px;line-height:1.2;color:#5a4337;font-weight:700}
.arrow{width:44px;height:40px;background:var(--brown-dark);display:flex;align-items:center;justify-content:center}
.arrow svg{width:14px;height:14px;fill:#fff}

/* featured */
.featured{top:734px;left:0;width:1200px;height:533px;background:var(--panel)}
.section-title{width:1200px;left:0;text-align:center;font-family:"Questrial",sans-serif;font-size:29px;color:#2b2b2b;letter-spacing:.5px}
.section-title span{color:var(--gold)}
.product{width:181px;top:109px;text-align:center}
.product .shot{width:181px;height:179px;background:var(--white);border:1px solid #bdbdbd;display:flex;align-items:center;justify-content:center}
.product .shot div{width:70px;height:130px;border-radius:8px}
.product h3{font-weight:400;font-size:13px;line-height:1.4;margin-top:18px;height:40px;color:#222}
.product .price{font-size:14px;margin-top:8px;color:#222}
.btn-buy{display:inline-block;margin-top:12px;background:var(--brown);color:#fff;font-family:"Questrial",sans-serif;font-size:14px;padding:6px 13px;border-radius:3px}
.view-all{left:494px;top:453px;width:212px;height:40px;border:1px solid #9a9a9a;border-radius:3px;background:#f6f6f6;font-family:"Questrial",sans-serif;font-size:17px;color:#333;display:flex;align-items:center;justify-content:center}

/* consultation */
.consult{top:1267px;left:0;width:1200px;height:434px;background:var(--white);overflow:hidden}
.consult-flowers{left:60px;top:100px;width:660px;height:334px;background:radial-gradient(ellipse at 45% 60%,#f1efe8 0%,#f7f6f2 55%,#ffffff 80%)}
.consult-photo{left:738px;top:0;width:462px;height:434px;background:linear-gradient(110deg,#e9edf0 0%,#d9dfe5 40%,#c8ccd0 100%)}
.consult h2{left:80px;top:70px;font-family:"Questrial",sans-serif;font-weight:400;font-size:30px;color:#2b2b2b}
.consult p{left:81px;top:118px;width:460px;font-size:15px;line-height:1.55;color:#222}
.btn-call{left:81px;top:201px;width:195px;height:38px;background:var(--brown);border-radius:4px;display:flex;align-items:center;gap:10px;padding-left:8px;color:#fff;font-family:"Questrial",sans-serif;font-size:19px}
.btn-call .ring{width:28px;height:28px;border:2px solid #fff;border-radius:50%;display:flex;align-items:center;justify-content:center}
.btn-call svg{width:14px;height:14px;fill:#fff}

/* blog */
.blog{top:1701px;left:0;width:1200px;height:379px;background:var(--white)}
.post-photo{width:167px;height:167px;border-radius:50%;border:3px double var(--gold-soft);padding:8px;top:119px}
.post-photo div{width:100%;height:100%;border-radius:50%}
.post{top:140px;width:300px}
.post h3{font-family:"Didact Gothic",sans-serif;font-weight:700;font-size:17px;color:var(--gold)}
.post .meta{display:flex;align-items:center;gap:8px;font-size:12px;margin-top:10px;color:#222}
.post .meta svg{width:15px;height:15px;fill:#333}
.post p{font-size:14px;line-height:1.35;margin-top:8px;color:#222}
.post .more{display:inline-block;margin-top:12px;font-size:13px;color:var(--gold);text-decoration:underline}
.divider{left:599px;top:122px;width:1px;height:170px;background:var(--line)}
.dots{left:575px;top:327px;display:flex;gap:6px;align-items:center}
.dots i{width:10px;height:10px;border-radius:50%;background:#555}
.dots i.on{width:16px;height:16px;background:var(--gold)}

/* footer */
.footer{top:2080px;left:0;width:1200px;height:217px;background:var(--footer);color:var(--footer-text);font-size:12px}
.footer h4{font-weight:400;font-size:13px;letter-spacing:.5px;color:#e4e4e4;display:flex;align-items:center;gap:8px}
.footer h4::after{content:"";display:block;height:1px;background:#555;width:70px}
.links{display:grid;grid-template-columns:103px 160px;row-gap:12px}
.addr{display:flex;gap:12px;line-height:1.45}
.addr svg{width:16px;height:16px;fill:#ddd;flex:none;margin-top:2px}
.field{width:204px;height:23px;background:#fff;color:#999;font-size:10px;padding:5px 6px}
.btn-sub{width:84px;height:23px;background:#555;color:#fff;font-size:12px;display:flex;align-items:center;justify-content:center;border:1px solid #888}
.social{display:flex;align-items:center;gap:12px}
.social .disc{width:36px;height:36px;border-radius:50%}
.social b{display:block;font-weight:400;font-size:14px;color:#eee}
.social small{font-size:10px;color:#999}
.bottombar{top:2297px;left:0;width:1200px;height:41px;background:var(--footer-bar);color:#ddd;font-size:12px}
.cards{display:flex;gap:6px;align-items:center}
.cards span{width:36px;height:22px;border-radius:3px;background:#e9e9e9}
</style>
</head>
<body>

<!-- top bar -->
<div class="abs topbar">
  <div class="abs item" style="left:536px"><svg viewBox="0 0 16 16"><circle cx="8" cy="5" r="3.5"/><path d="M1 16c0-4 3-6 7-6s7 2 7 6z"/></svg>Doctor</div>
  <div class="abs item" style="left:633px"><svg viewBox="0 0 16 16"><rect x="7" y="1" width="2" height="15"/><path d="M4 5h8l-2 2H6z"/></svg>Pharmacy</div>
  <div class="abs item" style="left:744px"><svg viewBox="0 0 16 16"><path d="M4 7V5a4 4 0 018 0v2h1v9H3V7zm2 0h4V5a2 2 0 00-4 0z"/></svg>Register / Log in</div>
  <div class="abs item" style="left:886px"><svg viewBox="0 0 16 16"><path d="M0 1h3l2 9h9l2-7H5"/><circle cx="6" cy="13.5" r="1.5"/><circle cx="13" cy="13.5" r="1.5"/></svg>Shopping Cart</div>
  <div class="abs lang"><span class="flag"></span>English <svg viewBox="0 0 10 10" style="width:9px;height:9px;margin-left:auto"><path d="M0 3h10L5 8z"/></svg></div>
</div>

<!-- header -->
<header class="abs header">
  <div class="abs logo"><span class="mark"></span>Velour Skinhaus</div>
  <div class="abs contact" style="left:683px">
    <span class="disc"><svg viewBox="0 0 20 20"><path d="M5 2l3 4-2 2c1 2 3 4 5 5l2-2 4 3-2 3C9 17 3 11 2 5z"/></svg></span>
    <div><small>Call Us Today</small><strong>+123-456-7890</strong></div>
  </div>
  <div class="abs contact" style="left:908px">
    <span class="disc"><svg viewBox="0 0 20 20"><path d="M2 5h16v10H2z M2 5l8 6 8-6" fill="none" stroke="#fff" stroke-width="1.8"/></svg></span>
    <div><small>Email Us</small><strong>info@velourskinhaus.com</strong></div>
  </div>
</header>

<!-- navigation -->
<nav class="abs nav">
  <a class="current" style="margin-right:66px">Home</a>
  <a style="margin-right:64px">Face</a>
  <a style="margin-right:64px">Body</a>
  <a style="margin-right:64px">Hair Care</a>
  <a style="margin-right:62px">Skin Concerns</a>
  <a style="margin-right:63px">Dermatologist Consultation</a>
  <a style="margin-right:63px">Library</a>
  <a>Contact Us</a>
</nav>

<!-- hero -->
<section class="abs hero">
  <div class="abs hero-photo" role="img" aria-label="Portrait of a woman applying cream to her cheek beside an orchid"></div>
  <div class="abs hero-products" role="img" aria-label="Cleansing tube, cream jar and toner bottle"></div>
  <h1 class="abs hero-title">Lorem ipsum dolor sit amet<br>consectetuer adipiscing</h1>
  <div class="abs arrow" style="left:5px;top:244px"><svg viewBox="0 0 14 14"><path d="M10 1L3 7l7 6z"/></svg></div>
  <div class="abs arrow" style="left:1152px;top:244px"><svg viewBox="0 0 14 14"><path d="M4 1l7 6-7 6z"/></svg></div>
</section>

<!-- featured products -->
<section class="abs featured">
  <h2 class="abs section-title" style="top:38px">FEATURED <span>PRODUCTS</span></h2>
  <div class="abs arrow" style="left:5px;top:248px;width:30px;height:30px"><svg viewBox="0 0 14 14"><path d="M10 1L3 7l7 6z"/></svg></div>
  <div class="abs arrow" style="left:1165px;top:248px;width:30px;height:30px"><svg viewBox="0 0 14 14"><path d="M4 1l7 6-7 6z"/></svg></div>

  <article class="abs product" style="left:81px">
    <div class="shot"><div role="img" aria-label="Silver serum pump bottle" style="width:40px;background:linear-gradient(90deg,#8e9094,#e3e4e6,#8e9094)"></div></div>
    <h3>Nullam euismod non nunc<br>lacinia aliquam</h3>
    <div class="price">$320.00</div><a class="btn-buy">BUY NOW</a>
  </article>
  <article class="abs product" style="left:294px">
    <div class="shot"><div role="img" aria-label="Olive toner bottle" style="width:42px;background:linear-gradient(90deg,#6e6a5e,#a9a493,#6e6a5e)"></div></div>
    <h3>Pharetr Massa, Eu Sodales<br>Nunc Posuere</h3>
    <div class="price">$210.00</div><a class="btn-buy">BUY NOW</a>
  </article>
  <article class="abs product" style="left:508px">
    <div class="shot"><div role="img" aria-label="Amber dropper bottle" style="width:50px;height:110px;background:linear-gradient(90deg,#6b3a1c,#b7672d,#6b3a1c)"></div></div>
    <h3>Quisque Accumsan Pharetr<br>Massa, Eu Sodales Nunc</h3>
    <div class="price">$350.00</div><a class="btn-buy">BUY NOW</a>
  </article>
  <article class="abs product" style="left:722px">
    <div class="shot"><div role="img" aria-label="Blue cleanser pump bottle" style="width:48px;background:linear-gradient(90deg,#5f97cc,#a9cdef,#5f97cc)"></div></div>
    <h3>Pharetr Massa, Eu Sodales<br>Nunc Posuere</h3>
    <div class="price">$150.00</div><a class="btn-buy">BUY NOW</a>
  </article>
  <article class="abs product" style="left:936px">
    <div class="shot"><div role="img" aria-label="Gold cream jar" style="width:120px;height:62px;background:linear-gradient(180deg,#d6ad4a,#8a6a1f)"></div></div>
    <h3>Pharetr Massa, Eu Sodales<br>Nunc Posuere</h3>
    <div class="price">$130.00</div><a class="btn-buy">BUY NOW</a>
  </article>

  <a class="abs view-all">VIEW ALL PRODUCTS</a>
</section>

<!-- dermatologist consultation -->
<section class="abs consult">
  <div class="abs consult-flowers" role="img" aria-label="Soft white daisies and a set of skincare bottles"></div>
  <div class="abs consult-photo" role="img" aria-label="Dermatologist examining a woman's skin with a magnifying glass"></div>
  <h2 class="abs">DERMATOLOGIST CONSULTATION</h2>
  <p class="abs">Lorem ipsum dolor sit amet, consectetuer adipiscing elit, sed diam nonummy nibh euismod tincidunt ut laoreet dolore magna aliquam erat volutpat. Ut wisi enim ad minim venia.</p>
  <a class="abs btn-call"><span class="ring"><svg viewBox="0 0 20 20"><path d="M5 2l3 4-2 2c1 2 3 4 5 5l2-2 4 3-2 3C9 17 3 11 2 5z"/></svg></span>CALL US TODAY</a>
</section>

<!-- blog -->
<section class="abs blog">
  <h2 class="abs section-title" style="top:60px">RECENT <span>BLOG POSTS</span></h2>

  <div class="abs post-photo" style="left:88px"><div role="img" aria-label="Blog portrait of a dark-haired woman" style="background:radial-gradient(circle,#e6c9b4,#8a6a55)"></div></div>
  <article class="abs post" style="left:271px">
    <h3>Lorem ipsum dolor sit amet</h3>
    <div class="meta">
      <svg viewBox="0 0 16 16"><circle cx="8" cy="8" r="7" fill="none" stroke="#333" stroke-width="1.6"/><path d="M7.2 4h1.6v4.2l3 1.8-.8 1.3-3.8-2.3z"/></svg>01 Sept, 2016
      <svg viewBox="0 0 16 16" style="margin-left:8px"><path d="M8 15L2 9A3.5 3.5 0 018 4a3.5 3.5 0 016 5z"/></svg>227
      <svg viewBox="0 0 16 16" style="margin-left:8px"><path d="M1 3h10v6H5l-3 3V9H1z M6 10h6l3 3v-3h1V5h-3v5"/></svg>2285
    </div>
    <p>Lorem ipsum dolor sit amet, sed dianummy nibh euismod tincidunt ut dolore. Lorem ipsum dolor ipsum dolor sit.</p>
    <a class="more">Read More</a>
  </article>

  <div class="abs divider"></div>

  <div class="abs post-photo" style="left:630px"><div role="img" aria-label="Blog portrait of a blonde woman" style="background:radial-gradient(circle,#e8d2b8,#5c4a3a)"></div></div>
  <article class="abs post" style="left:813px">
    <h3>Lorem ipsum dolor sit amet</h3>
    <div class="meta">
      <svg viewBox="0 0 16 16"><circle cx="8" cy="8" r="7" fill="none" stroke="#333" stroke-width="1.6"/><path d="M7.2 4h1.6v4.2l3 1.8-.8 1.3-3.8-2.3z"/></svg>01 Sept, 2016
      <svg viewBox="0 0 16 16" style="margin-left:8px"><path d="M8 15L2 9A3.5 3.5 0 018 4a3.5 3.5 0 016 5z"/></svg>227
      <svg viewBox="0 0 16 16" style="margin-left:8px"><path d="M1 3h10v6H5l-3 3V9H1z M6 10h6l3 3v-3h1V5h-3v5"/></svg>2285
    </div>
    <p>Lorem ipsum dolor sit amet, sed dianummy nibh euismod tincidunt ut dolore. Lorem ipsum dolor ipsum dolor sit.</p>
    <a class="more">Read More</a>
  </article>

  <div class="abs dots"><i></i><i class="on"></i><i></i></div>
</section>

<!-- footer -->
<footer class="abs footer">
  <div class="abs" style="left:81px;top:28px">
    <h4>QUICK LINKS</h4>
    <div class="links" style="margin-top:16px">
      <a>Home</a><a>Dermatologist Consultation</a>
      <a>Face</a><a>Library</a>
      <a>Body</a><a>Contact Us</a>
      <a>Hair Care</a><a>Register</a>
      <a>Skin Concerns</a><span></span>
    </div>
  </div>

  <div class="abs" style="left:388px;top:28px;width:260px">
    <h4>CONTACT ADDRESS</h4>
    <div class="addr" style="margin-top:16px"><svg viewBox="0 0 16 16"><path d="M8 0a5 5 0 00-5 5c0 4 5 11 5 11s5-7 5-11a5 5 0 00-5-5zm0 7a2 2 0 110-4 2 2 0 010 4z"/></svg><span>Vestibulum tristique ati eros &nbsp;Maecenas elit lion Pharetr Massa, Eu Sodales Nunc Posuere<br>Street no:2</span></div>
    <div class="addr" style="margin-top:12px"><svg viewBox="0 0 16 16"><rect x="4" y="0" width="8" height="16" rx="1.5"/></svg><span style="font-size:13px">+123-456-7890</span></div>
    <div class="addr" style="margin-top:12px"><svg viewBox="0 0 16 16"><path d="M1 6l7-5 7 5v9H1z" /></svg><span>info@velourskinhaus.com</span></div>
  </div>

  <div class="abs" style="left:682px;top:28px">
    <h4>NEWSLETTER &nbsp;SIGNUP</h4>
    <p style="margin-top:16px;font-size:11px">Signup with us and get update in your inbox.</p>
    <div class="field" style="margin-top:14px">Your Name</div>
    <div class="field" style="margin-top:12px">Email address</div>
    <div class="btn-sub" style="margin-top:12px">Subscribe</div>
  </div>

  <div class="abs" style="left:961px;top:28px">
    <h4>SOCIAL CONNECT</h4>
    <div class="social" style="margin-top:16px"><span class="disc" style="background:#3b5998"></span><div><b>Friendwall</b><small>Become A Fan</small></div></div>
    <div class="social" style="margin-top:10px"><span class="disc" style="background:#d34836"></span><div><b>Circlenet</b><small>Add To Circles</small></div></div>
    <div class="social" style="margin-top:10px"><span class="disc" style="background:#1da1f2"></span><div><b>Chirpline</b><small>Join Now</small></div></div>
  </div>
</footer>

<div class="abs bottombar">
  <span class="abs" style="left:81px;top:14px">Copyright © 2016 Velour Skinhaus. All Rights Reserved.</span>
  <div class="abs cards" style="left:843px;top:9px"><span style="width:auto;height:auto;background:none;color:#ddd;margin-right:6px">We Accept :</span><span></span><span></span><span></span><span></span><span></span></div>
</div>

</body>
</html>
```